Flyer-Design für bildenden Künstler
Zielgruppe
Ich bin bildender Künstler, benötige einen außergewöhnlichen, sehr ästhetischen, einzigartigen, als Eyecatcher fungierenden, meine Kunst und Identität repräsentierenden Flyer zum Auslegen, um neue KundInnen zu gewinnen.
Aufgabenstellung
Er soll wenig Text beinhalten (ein Zitat, Anschrift und Kontaktmöglichkeiten, ein kleines statement zu meiner Kunstphilosophie), und Bilder meiner Kunst zeigen. Raum ist mir wichtig, genug Leerräume, damit ein in Szene gesetztes Zitat oder Foto meiner Kunstwerke gut wirken kann. Es soll Lust darauf machen, Anreiz bieten und Interesse wecken, auf meine homepage zu gehen. Die Einzigartigkeit meiner Kunst soll deutlich werden.
Die hochgelandenen Fotos zeigen meine Kunstwerke. Sie können als Hintergrundbild fungieren und dementsprechend auch die ganze Seite ausfüllen, sie können zugeschnitten werden und/oder mit Text überlagert sein. Manche Fotos (zum Beispiel die Kunstwerke mit Rahmen) eignen sich dagegen, sie auf einer ganzen Seite zu zeigen, ohne einen Text dazu. So eine Seite würde ich jedenfalls gerne dabei haben, wo ein Kunstwerk für sich alleine auf einer ganzen Seite dargestellt wird. 1O4A2598 oder 1O4A6076a bieten sich dafür an (diese und alle anderen Fotos sind zum Teil komprimiert und zugeschnitten; falls gewünscht bzw. die Qualität nicht gut ist, kann ich das Originalfoto senden, das unkomprimiert und nicht zugeschnitten ist. Auch kann die Helligkeit oder die Farbqualität verbessert werden, falls notwendig). Nicht alle Kunstbilder müssen verwendet werden.
Ich bin offen für jedes Flyerformat, tendiere zu einem ein 2 oder 3-seitigen Falzflyer hochkant oder im Querformat. Bin aber offen für Ideen und Vorschläge.
Die Texte unter der Datei 'Texte, Adresse, Zitate' enthalten einen kleinen Text, der verwendet werden soll. Unter 'Text für die Titelseite' ist ein Vorschlag für die Titelseite zu finden. Die Adresse muss vollständig erscheinen, und unter 'Zitate' sind mehrere meiner Zitate - auch davon soll eines verwendet werden.
BITTE AUSSCHLIEßLICH DIE FOTOS UND TEXTE VERWENDEN, DIE ICH HOCHGELADEN HABE, UND NICHTS VON MEINEN HOMEPAGES NEHMEN. DANKE!

```html
<!DOCTYPE html>
<html lang="de">
<head>
<meta charset="utf-8">
<title>Fabian Wüstner Art – Transformationen</title>
<link rel="stylesheet" href="https://fonts.googleapis.com/css2?family=Comfortaa:wght@600&display=swap">
<style>
  :root {
    --rose-light: #e2b2ad;
    --rose-mid: #c98c8e;
    --rose-deep: #a66a76;
    --mauve: #8f6378;
    --title-white: #ffffff;
  }
  html, body {
    margin: 0;
    padding: 0;
    width: 1200px;
    height: 1200px;
    overflow: hidden;
  }
  .flyer-cover {
    position: relative;
    width: 1200px;
    height: 1200px;
    overflow: hidden;
    font-family: "Comfortaa", sans-serif;
  }
  .artwork-backdrop {
    position: absolute;
    inset: 0;
    background:
      radial-gradient(ellipse 30% 22% at 22% 70%, rgba(226,170,160,0.85), transparent 70%),
      radial-gradient(ellipse 28% 20% at 60% 88%, rgba(200,150,165,0.8), transparent 70%),
      radial-gradient(ellipse 35% 25% at 85% 75%, rgba(215,160,165,0.75), transparent 70%),
      radial-gradient(ellipse 40% 30% at 30% 20%, rgba(205,150,150,0.7), transparent 70%),
      radial-gradient(ellipse 40% 30% at 80% 25%, rgba(190,130,140,0.7), transparent 70%),
      linear-gradient(180deg, var(--rose-mid) 0%, var(--rose-light) 45%, var(--rose-deep) 75%, var(--mauve) 100%);
  }
  .cover-title {
    position: absolute;
    inset: 0;
    filter: drop-shadow(4px 5px 6px rgba(60, 30, 40, 0.45));
  }
  .cover-title text {
    fill: var(--title-white);
    font-family: "Comfortaa", sans-serif;
    font-weight: 600;
  }
</style>
</head>
<body>
  <main class="flyer-cover">
    <div class="artwork-backdrop" role="img" aria-label="Nahaufnahme eines Kunstwerks aus rosafarbenen, porösen Naturschwämmen"></div>
    <svg class="cover-title" width="1200" height="1200" viewBox="0 0 1200 1200">
      <text class="artist-name" x="114" y="290" font-size="205" textLength="1004" lengthAdjust="spacingAndGlyphs">fabian</text>
      <text class="artist-name" x="114" y="478" font-size="205" textLength="1004" lengthAdjust="spacingAndGlyphs">wüstner art</text>
      <text class="series-title" x="118" y="640" font-size="108" textLength="1008" lengthAdjust="spacingAndGlyphs">transformationen</text>
    </svg>
  </main>
</body>
</html>
```